Systems and Technology Consultants - Website

Design & Build a website for a new company which operates in the Systems and Technology space for Transportation, Government and Commercial sectors.

Overall design should be minimalist in nature.
Should also have a feed that provides news and event updates on the main page.
Logo has already been awarded and should be incorporated into the site.

We like the overall layout, functionality and simplicity of the below sites. Submitted designs could be similar to or a combination of the aspects on these sites, or perhaps a whole different concept - we are open to new ideas.
Norvique.com
Teblo.it

Update 1 Dated 27 May 2014

All I am moving away from the Teblo.it website and would like it to be more aligned with Norvique.com not only in layout but in functionality. I will be extending the deadline of this design brief for two weeks to incorporate additional requirements and will add addtional funding to the project.

Apologies for not having more information available to provide but with so many submissions its getting confusing.

Thanks Derek

Please note that the brief has been updated and the deadline has been extended.

Important: We will need two language versions of the website, English and Arabic; the website is hosted on HostPelican

Hello All, Thank you for your submissions. We have narrowed it down to the final 6 designers and I just wanted to take a moment and provide a bit of feedback regarding the concepts that we like and the modifications we are looking for. First, let me mention some of the design functions we like. - At the top of the homepage we really like the "region" or "language" tab so that the website can be viewed in both English and Arabic. - We like the homepage to have clear color variation so that the different sections of the homepage are distinct. Additionally, we like the bottom portion of the homepage to be in red. We feel that draws attention to our contact information. Again, we would like the colors to integrate black, gray-scale, red, etc. - Having a search tab at the top of the home page, or integrated into the main image, so that the site is easy to navigate. - We especially like the main image to have the scrolling tabs at the bottom so it is easy to browse the services offered (Consultancy, Solutions Architecture, Masters Systems Integration, Independent Design Review). - In regards to the services offered tab we really like the idea that a few people presented that have the outside of our logo with an icon in the middle of consultancy, solutions, etc., etc. Secondly, as mentioned in our brief we really enjoy the design of norvique site. Specially, we enjoy the strong iconic images they use, the way the tabs at the top scroll easily, and contact us page that generates an email. Lastly, I've included some photos of the concept we have been working on. What we are trying to demonstrate is how our company offers a range of services that are essentially linked together. We provide individual services that when combined present the full service package. We would like this concept to be integrated into the over concept of our website. Please feel free to ask for clarification of any of the above points or contact us if you have any additional questions. We appreciate all of your hard work and are very excited to see the updated designs. Best, Marta Vennick Quelbrant Senior Program Manager marta.vennick@quelbrant-example.com

Industry/Entity Type

Government

Font styles to use
Serif
Sans Serif

Requirements
Must have
• Must work on/adapt to various/mobile devices (responsive)
Must be simple and straightforward
Colors should be in line/matching with logo
2 language versions: English and Arabic (no Thai)
Services should be the first group/row of items after/below the main image
Note: the website will be hosted by hostpelican
Nice to have
• Submit feedback form
What's New section
The banner at the bottom of the site should not be too large; we would like a narrow one more
It would be nice if the header/top banner (with Home, About, etc. tabs) could stay in place as you scroll down (like Norvique and Chatterloop)
We will likely only use one image with a Company slogan on the Home page rather than a carousel of images to rotate through
Should not have
• This is the existing website: http://www.quelbrant-example.org
We do not like the animation, the way the banner icons/titles bounce
Not simple enough, we don't like the functionality or how pages load so slowly
We do not like the logo centered - it should be at the left
The banner and its tabs should not be towards the right, we would like them to be centered, to go all the way across and to be below the logo

```html
<!DOCTYPE html>
<html lang="en">
<head>
<meta charset="utf-8">
<title>Quelbrant – Systems Professionals</title>
<link href="https://fonts.googleapis.com/css2?family=Open+Sans:ital,wght@0,400;0,600;1,400&family=Arimo:ital,wght@0,400;1,400&family=Tinos:ital,wght@0,400;1,400;1,700&display=swap" rel="stylesheet">
<style>
:root{
  --red:#e3161e;
  --dark:#333333;
  --text:#555555;
  --muted:#8a8a8a;
  --line:#dddddd;
  --band:#f2f2f2;
  --footer:#3a3a3a;
  --hero-deep:#0a3d78;
  --hero-light:#3c8fd6;
}
*{box-sizing:border-box;margin:0;padding:0}
html,body{width:707px;height:1200px;overflow:hidden;background:#fff}
body{position:relative;font-family:"Open Sans",Arial,sans-serif;color:var(--text)}
.abs{position:absolute}

/* top bar */
.topbar{left:0;top:0;width:707px;height:26px;background:#f5f5f5;border-top:2px solid var(--red);border-bottom:1px solid #e3e3e3;font-size:7px;color:#555}
.topbar span{position:absolute;top:7px;display:flex;align-items:center;gap:3px}

/* header */
.brand{left:78px;top:33px;width:54px;text-align:center}
.brand-mark{display:block;margin:0 auto 3px;width:18px;height:18px;background:var(--red);border-radius:50%}
.brand-name{font-size:8px;font-weight:600;color:var(--red);letter-spacing:1px}
.search{left:456px;top:30px;width:173px;height:20px;display:flex}
.search-input{flex:1;border:1px solid #ddd;font-size:7.5px;color:#999;padding:5px 8px}
.search-btn{width:44px;background:var(--red);color:#fff;font-size:7.5px;font-weight:600;text-align:center;line-height:20px}
.nav{left:260px;top:65px;width:370px;display:flex;justify-content:space-between;font-size:7.5px;color:#444;letter-spacing:.2px}
.nav .active{color:var(--red)}

/* hero */
.hero{left:0;top:82px;width:707px;height:262px;background:radial-gradient(circle at 18% 48%,var(--hero-light) 0%,#1d5fa8 30%,var(--hero-deep) 70%),var(--hero-deep)}
.hero-title{left:285px;top:121px;font-size:32px;color:#fff;font-weight:400;white-space:nowrap}
.hero-copy{left:289px;top:175px;width:330px;font-size:7.4px;line-height:17.6px;color:#fff}
.hero-btn{left:289px;top:258px;width:135px;height:28px;border:1px solid #fff;color:#fff;font-size:8px;text-align:center;line-height:26px}
.hero-arrow{top:202px}

/* welcome */
.welcome-title{left:0;top:363px;width:707px;text-align:center;font-size:14px;color:var(--dark);font-weight:600}
.welcome-copy{left:86px;top:392px;width:535px;text-align:center;font-size:6.4px;line-height:17px;color:#888}

/* features */
.features{left:0;top:450px;width:707px;height:102px;background:var(--band) repeating-linear-gradient(45deg,rgba(0,0,0,.025) 0 1px,transparent 1px 4px)}
.feature{top:14px;width:176px}
.feature-icon{position:absolute;left:0;top:0}
.feature-title{position:absolute;left:44px;top:5px;font-size:10px;color:#333}
.feature-sub{position:absolute;left:44px;top:19px;font-size:6px;font-style:italic;color:var(--red);font-family:Arimo,Arial,sans-serif}
.feature-text{position:absolute;left:2px;top:41px;width:174px;font-size:6.4px;line-height:12px;color:#888}

/* services */
.section-title{font-size:11px;font-weight:600;color:var(--dark)}
.svc-arrows{left:605px;top:574px;display:flex;gap:2px}
.svc-arrows i{display:block;width:11px;height:11px;background:#aaa}
.card{top:598px;width:129px;height:193px;border:1px solid #e3e3e3;background:#fff}
.card-img{position:absolute;left:5px;top:5px;width:119px;height:102px}
.card-title{position:absolute;left:4px;top:117px;font-size:7.6px;color:var(--red)}
.card-text{position:absolute;left:4px;top:137px;width:122px;font-family:Arimo,Arial,sans-serif;font-style:italic;font-size:6.2px;line-height:12px;color:#666}
.card-text em{color:var(--red)}

/* news */
.news-item{left:78px;width:267px}
.news-img{position:absolute;left:0;top:0;width:79px;height:75px}
.news-title{position:absolute;left:98px;top:0;font-size:9px;color:var(--red)}
.news-meta{position:absolute;left:98px;top:19px;width:168px;font-size:5.5px;color:#aaa;padding-bottom:6px;border-bottom:1px solid #ddd}
.news-text{position:absolute;left:98px;top:39px;width:170px;font-size:6.3px;line-height:12.7px;color:#666}
.news-rule{left:78px;top:934px;width:267px;border-top:1px solid #e5e5e5}

/* testimonial */
.quote{left:377px;top:846px;width:246px;font-size:6.3px;line-height:16.8px;color:#555}
.quote-mark{font-family:Tinos,serif;font-size:18px;color:#666;line-height:1}
.quote-name{left:520px;top:990px;width:109px;text-align:right;font-family:Tinos,serif;font-size:8.5px;color:var(--red)}
.quote-date{left:520px;top:1005px;width:98px;text-align:right;font-family:Tinos,serif;font-size:5px;color:#777}

/* newsletter */
.newsletter{left:77px;top:1049px;width:553px;height:80px;border:1px solid #e3e3e3;background:linear-gradient(#f7f7f7,#ececec)}
.nl-title{position:absolute;left:4px;top:21px;font-family:Tinos,serif;font-style:italic;font-size:17px;color:#444}
.nl-input{position:absolute;left:161px;top:20px;width:271px;height:29px;border:1px solid #ccc;background:#fff;font-family:Tinos,serif;font-style:italic;font-size:6.5px;color:#555;padding:10px 8px}
.nl-btn{position:absolute;left:449px;top:20px;width:95px;height:28px;background:linear-gradient(#555,#222);color:#fff;font-family:Tinos,serif;font-style:italic;font-size:8.5px;text-align:center;line-height:28px;letter-spacing:.3px}

/* footer */
.footer{left:0;top:1142px;width:707px;height:58px;background:var(--footer);color:#fff;font-family:Arimo,Arial,sans-serif}
.footer-nav{position:absolute;left:78px;top:15px;font-size:6.4px}
.footer-nav b{font-weight:400;margin:0 6px}
.footer-copy{position:absolute;left:78px;top:35px;font-size:6.2px}
.social{position:absolute;left:522px;top:19px;display:flex;gap:4px}
.social i{display:block;width:18px;height:18px;border:1.2px solid #fff;border-radius:50%}
</style>
</head>
<body>

<div class="topbar abs">
  <span style="left:78px">
    <svg width="7" height="7" viewBox="0 0 10 10"><path d="M2 1l2 2-1 1.5a6 6 0 0 0 2.5 2.5L7 6l2 2-1.5 1.5C4.5 9 1 5.5.5 2.5z" fill="#555"/></svg>66 -041-555-207
    <svg style="margin-left:10px" width="8" height="7" viewBox="0 0 10 9"><path d="M1 1h8v5H4L2 8V6H1z" fill="#555"/></svg>Live Chat
  </span>
  <span style="right:78px">
    <svg width="8" height="6" viewBox="0 0 10 7"><rect width="10" height="7" fill="#555"/><path d="M0 0l5 4 5-4" stroke="#f5f5f5" fill="none"/></svg>Email: info@quelbrant-example.org
  </span>
</div>

<header>
  <div class="brand abs"><span class="brand-mark"></span><span class="brand-name">QUELBRANT</span></div>
  <div class="search abs"><div class="search-input">Article</div><div class="search-btn">SEARCH</div></div>
  <nav class="nav abs">
    <span class="active">HOME</span><span>BUSINESS UNITS</span><span>SERVICES</span><span>ABOUT US</span><span>LOCATIONS</span><span>CONTACT US</span>
  </nav>
</header>

<section class="hero abs" role="img" aria-label="Glowing blue globe with network lines on a deep blue background"></section>
<svg class="abs hero-arrow" style="left:43px" width="22" height="22" viewBox="0 0 22 22"><circle cx="11" cy="11" r="10" fill="none" stroke="#fff" stroke-width="1.5"/><path d="M13 6l-5 5 5 5" fill="none" stroke="#fff" stroke-width="2"/></svg>
<svg class="abs hero-arrow" style="left:639px" width="22" height="22" viewBox="0 0 22 22"><circle cx="11" cy="11" r="10" fill="none" stroke="#fff" stroke-width="1.5"/><path d="M9 6l5 5-5 5" fill="none" stroke="#fff" stroke-width="2"/></svg>
<h1 class="hero-title abs">Systems Professionals</h1>
<p class="hero-copy abs">quelbrant specializes in delivering quality professional services and technical projects that support larger business goals.&nbsp; systems are tools that support a greater business function and need. we understand that most technical projects are conceptualized to support a larger vision mind and ensure that all of our professional and certified expertise.........</p>
<div class="hero-btn abs">CLICK HERE FOR MORE INFO</div>

<h2 class="welcome-title abs">Welcome to Our Company</h2>
<p class="welcome-copy abs">Quelbrant is a joint venture between varnel construction, orvik worldwide and tesk engineering &amp; management company founded in bangkok, thailand in 2003 and brelo electrical construction company founded in san francisco, california in 2001. developed by former calderon telecom, halvern and pell and morrow employees with over 30 years experience in engineering and construction of systems around the globe.</p>

<section class="features abs">
  <div class="feature abs" style="left:80px">
    <svg class="feature-icon" width="33" height="33" viewBox="0 0 33 33"><circle cx="16.5" cy="16.5" r="15.5" fill="#fff" stroke="#e3161e" stroke-width="1.5"/><circle cx="16.5" cy="13" r="3" fill="#555"/><circle cx="11" cy="14" r="2.3" fill="#555"/><circle cx="22" cy="14" r="2.3" fill="#555"/><path d="M11 22a5.5 5 0 0 1 11 0zM6.5 21a4.5 4 0 0 1 6-3.5M26.5 21a4.5 4 0 0 0-6-3.5" fill="#555"/></svg>
    <div class="feature-title">Consulting</div>
    <div class="feature-sub">tristique senectus malesuada</div>
    <p class="feature-text">Pellentesque habitant morbi tristique senectus et netus et malesuada fames ac turpis egestas. Vestibulum tortor quam.......</p>
  </div>
  <div class="feature abs" style="left:268px">
    <svg class="feature-icon" width="33" height="33" viewBox="0 0 33 33"><circle cx="16.5" cy="16.5" r="15.5" fill="#fff" stroke="#e3161e" stroke-width="1.5"/><path d="M9 22h15v2H9zM12 21l3-7h3l2 4h-3z" fill="#555"/><path d="M15 14l-3-4" stroke="#555" stroke-width="1.5"/></svg>
    <div class="feature-title">Construction</div>
    <div class="feature-sub">tristique senectus malesuada</div>
    <p class="feature-text">Pellentesque habitant morbi tristique senectus et netus et malesuada fames ac turpis egestas. Vestibulum tortor quam.......</p>
  </div>
  <div class="feature abs" style="left:456px">
    <svg class="feature-icon" width="33" height="33" viewBox="0 0 33 33"><circle cx="16.5" cy="16.5" r="15.5" fill="#fff" stroke="#e3161e" stroke-width="1.5"/><circle cx="16.5" cy="16.5" r="6" fill="none" stroke="#555" stroke-width="3" stroke-dasharray="2.5 1.5"/><circle cx="16.5" cy="16.5" r="2.5" fill="#555"/></svg>
    <div class="feature-title">Maintenance</div>
    <div class="feature-sub">tristique senectus malesuada</div>
    <p class="feature-text">Pellentesque habitant morbi tristique senectus et netus et malesuada fames ac turpis egestas. Vestibulum tortor quam.......</p>
  </div>
</section>

<h2 class="section-title abs" style="left:78px;top:573px">Our Services</h2>
<div class="svc-arrows abs"><i></i><i></i></div>

<article class="card abs" style="left:78px">
  <div class="card-img" role="img" aria-label="Blue circuit board photo" style="background:linear-gradient(135deg,#0b3f7a,#2a9ad8)"></div>
  <div class="card-title">Systems Design &amp; Engineering</div>
  <p class="card-text">quelbrant recognizes the middle east and greater asia regions are economic growth markets infrastructure recognizes projects ..........<em>READ MORE</em></p>
</article>
<article class="card abs" style="left:218px">
  <div class="card-img" role="img" aria-label="Light blue puzzle globe photo" style="background:linear-gradient(135deg,#e9f6fb,#7fc0dd)"></div>
  <div class="card-title">Systems Integration</div>
  <p class="card-text">quelbrant recognizes the middle east and greater asia regions are economic growth markets infrastructure recognizes projects ..........<em>READ MORE</em></p>
</article>
<article class="card abs" style="left:361px">
  <div class="card-img" role="img" aria-label="Rolled blueprint plans photo" style="background:linear-gradient(135deg,#1b4f88,#8db8e0)"></div>
  <div class="card-title">Special Airport Systems</div>
  <p class="card-text">quelbrant recognizes the middle east and greater asia regions are economic growth markets infrastructure recognizes projects ..........<em>READ MORE</em></p>
</article>
<article class="card abs" style="left:500px">
  <div class="card-img" role="img" aria-label="Blue process flowchart photo" style="background:linear-gradient(135deg,#163e78,#4f8fd0)"></div>
  <div class="card-title">Systems Project Management</div>
  <p class="card-text">quelbrant recognizes the middle east and greater asia regions are economic growth markets infrastructure recognizes projects ..........<em>READ MORE</em></p>
</article>

<h2 class="section-title abs" style="left:78px;top:817px">News &amp; Events</h2>
<article class="news-item abs" style="top:847px;height:76px">
  <div class="news-img" role="img" aria-label="Industrial cable trays photo" style="background:linear-gradient(135deg,#6b4a2c,#c79a5e)"></div>
  <div class="news-title">Consequat Qonvallis</div>
  <div class="news-meta">&#9719;&nbsp; MARCH 2,2014 &nbsp;&nbsp;&nbsp;&nbsp; &#9632; 3 CIMMENTS</div>
  <p class="news-text">quelbrant specializes in delivering quality professional services and technical projects that support larger business goals.......</p>
</article>
<div class="news-rule abs"></div>
<article class="news-item abs" style="top:950px;height:76px">
  <div class="news-img" role="img" aria-label="Industrial plant under blue sky photo" style="background:linear-gradient(#3f7fc6,#5a6a7c)"></div>
  <div class="news-title">Consequat Qonvallis</div>
  <div class="news-meta">&#9719;&nbsp; MARCH 2,2014 &nbsp;&nbsp;&nbsp;&nbsp; &#9632; 3 CIMMENTS</div>
  <p class="news-text">quelbrant specializes in delivering quality professional services and technical projects that support larger business goals.......</p>
</article>

<h2 class="section-title abs" style="left:360px;top:817px">Testimonials</h2>
<span class="quote-mark abs" style="left:362px;top:843px">&ldquo;</span>
<p class="quote abs">Quelbrant is a joint venture between varnel construction, orvik worldwide and tesk engineering &amp; management company founded in bangkok, thailand in 2003 and brelo electrical construction company founded in san francisco, california in 2001. developed by former calderon telecom, halvern and pell and morrow related and interdependent support services can be incorporated into and provided as part of our professional services nia in 2001. developed by former calderon telecom, halvern and pell and morrow related and interdependent supcan be incorporated into and provided as part of our professional services</p>
<span class="quote-mark abs" style="left:603px;top:970px">&rdquo;</span>
<div class="quote-name abs">Evan Tollard</div>
<div class="quote-date abs">on 22 apr 2014</div>

<section class="newsletter abs">
  <div class="nl-title">Newsletter Sign up :</div>
  <div class="nl-input">Enter Your Email ID :</div>
  <div class="nl-btn">SUBSCRIBE</div>
</section>

<footer class="footer abs">
  <div class="footer-nav">Home<b>|</b>Business Units<b>|</b>Services<b>|</b>About Us<b>|</b>Locations<b>|</b>Contact Us</div>
  <div class="footer-copy">Copy Right 2014 Quelbrant.All Right Reseved.</div>
  <div class="social"><i></i><i></i><i></i><i></i><i></i></div>
</footer>

</body>
</html>
```